Business Card Design

I already have a company logo for my company. I have a logo for the manufacturer we represent. I want a professional business card design.

```html
<!DOCTYPE html>
<html lang="en">
<head>
<meta charset="utf-8">
<title>Business Card — Front and Back</title>
<link rel="stylesheet" href="https://fonts.googleapis.com/css2?family=Poppins:ital,wght@0,400;0,500;0,600;0,700;1,400&display=swap">
<style>
  :root {
    --brand-red: #d9111c;
    --ink: #161616;
    --card-white: #f6f6f4;
    --card-black: #141414;
    --stage: #e4e5e8;
    --muted: #444;
    --faint: #ececea;
  }
  * { box-sizing: border-box; margin: 0; padding: 0; }
  html, body {
    width: 1200px; height: 900px; overflow: hidden;
    background: var(--stage);
    font-family: "Poppins", sans-serif;
    color: var(--ink);
  }
  .stage {
    width: 1200px; height: 900px;
    display: flex; align-items: center; justify-content: center; gap: 40px;
  }
  .card {
    position: relative;
    width: 520px; height: 297px;
    overflow: hidden;
    box-shadow: 0 18px 40px rgba(0,0,0,.18);
  }

  /* Front */
  .card--front { background: var(--card-white); }
  .front__watermark {
    position: absolute; right: 40px; top: -60px;
    width: 300px; height: 300px; border-radius: 50%;
    background: var(--faint);
  }
  .brand {
    position: absolute; display: flex; align-items: center; gap: 10px;
    font-weight: 700; color: var(--brand-red); line-height: 1.05;
    text-transform: uppercase; letter-spacing: .5px;
  }
  .brand__dot { width: 34px; height: 34px; border-radius: 50%; background: var(--brand-red); flex: none; }
  .card--front .brand { left: 30px; top: 58px; font-size: 19px; }

  .person { position: absolute; right: 34px; top: 34px; text-align: right; }
  .person__name { font-size: 22px; font-weight: 400; letter-spacing: .3px; }
  .person__name strong { color: var(--brand-red); font-weight: 600; }
  .person__role { font-size: 15px; font-style: italic; color: var(--muted); }

  .rule { position: absolute; height: 2px; background: var(--brand-red); }
  .rule--right { right: 0; top: 108px; width: 250px; }
  .rule--left { left: 30px; top: 190px; width: 250px; }

  .address {
    position: absolute; left: 290px; top: 130px;
    display: flex; gap: 8px; font-size: 14px; line-height: 1.4;
  }
  .contacts { position: absolute; left: 30px; top: 204px; list-style: none; }
  .contacts li { display: flex; align-items: center; gap: 8px; font-size: 14px; line-height: 1.55; }
  .icon {
    width: 16px; height: 16px; border-radius: 50%; background: var(--brand-red);
    display: inline-flex; align-items: center; justify-content: center; flex: none;
  }
  .icon svg { width: 10px; height: 10px; }
  .address .icon { margin-top: 3px; }

  /* Back */
  .card--back { background: var(--card-black); }
  .card--back .brand { left: 50%; top: 50%; transform: translate(-50%, -50%); font-size: 24px; }
  .card--back .brand__dot { width: 42px; height: 42px; }
  .back__stripes { position: absolute; right: 0; top: 0; width: 170px; height: 297px; }
</style>
</head>
<body>
<main class="stage">
  <section class="card card--front" aria-label="Card front">
    <div class="front__watermark" aria-hidden="true"></div>
    <div class="brand"><span class="brand__dot"></span><span>Beacon<br>Signal Group</span></div>

    <div class="person">
      <p class="person__name">SAMPLE <strong>NAME</strong></p>
      <p class="person__role">Designation</p>
    </div>
    <div class="rule rule--right"></div>

    <div class="address">
      <span class="icon"><svg viewBox="0 0 10 10"><path d="M5 1a3 3 0 0 0-3 3c0 2.2 3 5 3 5s3-2.8 3-5a3 3 0 0 0-3-3zm0 4a1 1 0 1 1 0-2 1 1 0 0 1 0 2z" fill="#fff"/></svg></span>
      <p>123, ABC Street,<br>Area Name City Name,<br>Country 0000</p>
    </div>

    <div class="rule rule--left"></div>
    <ul class="contacts">
      <li><span class="icon"><svg viewBox="0 0 10 10"><path d="M2.5 1.5l1.5 0 .6 2-1 .7a5 5 0 0 0 2.2 2.2l.7-1 2 .6v1.5a1 1 0 0 1-1 1A6.5 6.5 0 0 1 1.5 2.5a1 1 0 0 1 1-1z" fill="#fff"/></svg></span>+00 123 456789</li>
      <li><span class="icon"><svg viewBox="0 0 10 10"><rect x="1.5" y="2.5" width="7" height="5" fill="none" stroke="#fff"/><path d="M1.5 2.5l3.5 3 3.5-3" fill="none" stroke="#fff"/></svg></span>email@website.com</li>
      <li><span class="icon"><svg viewBox="0 0 10 10"><circle cx="5" cy="5" r="3.5" fill="none" stroke="#fff"/><path d="M1.5 5h7M5 1.5c-2 2.3-2 4.7 0 7M5 1.5c2 2.3 2 4.7 0 7" fill="none" stroke="#fff" stroke-width=".7"/></svg></span>www.website.com</li>
    </ul>
  </section>

  <section class="card card--back" aria-label="Card back">
    <svg class="back__stripes" viewBox="0 0 170 297" aria-hidden="true">
      <polygon points="20,0 50,0 110,297 80,297" fill="var(--brand-red)"/>
      <polygon points="70,0 100,0 160,297 130,297" fill="var(--brand-red)"/>
      <polygon points="120,0 145,0 170,120 170,240" fill="var(--brand-red)"/>
    </svg>
    <div class="brand"><span class="brand__dot"></span><span>Beacon<br>Signal Group</span></div>
  </section>
</main>
</body>
</html>
```